Modern Business Card

Modern professional business card with more than just logo and demographic info. Something memorable.

We are a trendy/modern chiropractic group with an emphasis on neurology, hence the minimalist-type brain logo. We want to convey that modern and technical aspect with professionalism and the elite nature of our practice environment.

```html
<!DOCTYPE html>
<html lang="en">
<head>
<meta charset="utf-8">
<title>Vantage Chiropractic – Business Card</title>
<link rel="stylesheet" href="https://fonts.googleapis.com/css2?family=Lora:wght@400;500&family=Saira+Semi+Condensed:wght@500&display=swap">
<style>
  :root {
    --backdrop: #b9b9b9;
    --brand-blue: #3d63a0;
    --brand-blue-deep: #365a94;
    --card-white: #f4f4f3;
    --ink-dark: #2b2326;
    --wave-dark: #3a2d31;
    --ink-grey: #3f3f44;
    --on-blue: #eef0f5;
  }
  * { box-sizing: border-box; margin: 0; padding: 0; }
  html, body {
    width: 1200px; height: 576px; overflow: hidden;
    background: var(--backdrop);
  }
  .stage { position: relative; width: 1200px; height: 576px; }

  .card {
    position: absolute;
    top: 139px;
    width: 482px; height: 292px;
    border-radius: 12px;
    overflow: hidden;
  }

  /* Front */
  .card-front {
    left: 82px;
    background: var(--brand-blue);
    display: flex; flex-direction: column;
    align-items: center; justify-content: center;
  }
  .front-wordmark {
    font-family: "Lora", serif;
    font-weight: 400;
    color: var(--on-blue);
    text-align: center;
    line-height: 1;
    margin-top: -8px;
  }
  .front-wordmark .word-main { display: block; font-size: 58px; letter-spacing: 1px; }
  .front-wordmark .word-sub { display: block; font-size: 29px; letter-spacing: 0.5px; margin-top: 2px; }

  /* Back */
  .card-back { left: 602px; background: var(--card-white); }
  .back-wave { position: absolute; inset: 0; width: 482px; height: 292px; }

  .brand-mark {
    position: absolute; left: 97px; top: 50px;
    width: 70px; height: 70px;
    background: var(--brand-blue);
    border-radius: 6px;
  }

  .back-wordmark {
    position: absolute; left: 30px; top: 139px; width: 204px;
    font-family: "Lora", serif; font-weight: 400;
    color: var(--ink-dark);
    line-height: 1; text-align: center;
  }
  .back-wordmark .word-main { display: block; font-size: 35px; letter-spacing: 0.5px; }
  .back-wordmark .word-sub { display: block; font-size: 17px; letter-spacing: 0.4px; margin-top: 1px; }

  .holder {
    position: absolute; right: 31px; top: 42px;
    text-align: right;
  }
  .holder-name {
    font-family: "Saira Semi Condensed", sans-serif; font-weight: 500;
    font-size: 20px; color: var(--brand-blue); line-height: 1.2;
  }
  .holder-role, .holder-address {
    font-family: "Lora", serif; font-size: 12px; color: var(--ink-grey);
  }
  .holder-role { margin-top: 3px; }
  .holder-address { margin-top: 18px; line-height: 1.5; }

  .contact-list {
    position: absolute; right: 31px; top: 206px;
    list-style: none; text-align: right;
    font-family: "Lora", serif; font-size: 12px; color: var(--on-blue);
  }
  .contact-list li {
    display: flex; justify-content: flex-end; align-items: center;
    gap: 7px; height: 18.5px;
  }
  .contact-icon { width: 11px; height: 11px; fill: var(--on-blue); }
</style>
</head>
<body>
<main class="stage">

  <section class="card card-front" aria-label="Business card front">
    <h1 class="front-wordmark">
      <span class="word-main">VANTAGE</span>
      <span class="word-sub">CHIROPRACTIC</span>
    </h1>
  </section>

  <section class="card card-back" aria-label="Business card back">
    <svg class="back-wave" viewBox="0 0 482 292" aria-hidden="true">
      <path fill="var(--brand-blue-deep)" d="M0,256 C60,286 150,292 222,278 C292,264 338,206 390,190 C430,178 460,174 482,174 L482,292 L0,292 Z"/>
      <path fill="var(--wave-dark)" d="M0,222 C70,250 160,262 230,252 C290,240 330,200 380,175 C420,160 460,154 482,154 L482,164 C450,166 415,172 380,182 C330,198 300,256 230,264 C150,274 60,266 0,244 Z"/>
    </svg>

    <div class="brand-mark" aria-hidden="true"></div>

    <h2 class="back-wordmark">
      <span class="word-main">VANTAGE</span>
      <span class="word-sub">CHIROPRACTIC</span>
    </h2>

    <div class="holder">
      <p class="holder-name">Daniel Rowe</p>
      <p class="holder-role">Managing Director</p>
      <p class="holder-address">58 Meadow Lane, Fairview,<br>Harbor County, US 204518</p>
    </div>

    <ul class="contact-list">
      <li>555-201-4830
        <svg class="contact-icon" viewBox="0 0 12 12"><path d="M1 4 C1 2 3 1 6 1 C9 1 11 2 11 4 L9 5 L8 3.5 C7 3.2 5 3.2 4 3.5 L3 5 Z M3 6 H9 L10 11 H2 Z"/></svg>
      </li>
      <li>vantagechiro.com
        <svg class="contact-icon" viewBox="0 0 12 12"><path d="M1 2.5 H11 V9.5 H1 Z"/><path d="M1 2.5 L6 6.5 L11 2.5" fill="none" stroke="var(--brand-blue-deep)" stroke-width="1"/></svg>
      </li>
      <li>daniel@vantagechiro.com
        <svg class="contact-icon" viewBox="0 0 12 12"><circle cx="6" cy="6" r="5"/><path d="M1 6 H11 M6 1 C3.5 3.5 3.5 8.5 6 11 M6 1 C8.5 3.5 8.5 8.5 6 11" fill="none" stroke="var(--brand-blue-deep)" stroke-width="0.8"/></svg>
      </li>
    </ul>
  </section>

</main>
</body>
</html>
```